Business Card Design

New business card design

Target Market(s)

Residential & Commercial Property Managers

Industry/Entity Type

Plumbing Services

Contact Information for Business Card

Name - Rowan Keddle, title - Director, Phone Number - 0431 286 517, email - rowan@tbk-plumbing.com.au, Company ABN - 73 215 904 386,

Font styles to use
Sans Serif

Colors
0054AA
0677BA
7BADD7
CADEEF
E8F1F8

```html
<!DOCTYPE html>
<html lang="en">
<head>
<meta charset="utf-8">
<title>TBK Plumbing Services – Business Card</title>
<link href="https://fonts.googleapis.com/css2?family=Roboto:wght@300;400;700&display=swap" rel="stylesheet">
<style>
  :root {
    --page-bg: #efefef;
    --card-white: #ffffff;
    --brand-blue: #00aaeb;
    --brand-blue-deep: #0094cf;
    --band-dark: #1f242a;
    --ink: #23272c;
    --muted: #6b6f74;
    --on-dark: #f2f4f6;
  }
  * { margin: 0; padding: 0; box-sizing: border-box; }
  html, body {
    width: 1200px; height: 900px; overflow: hidden;
    background: var(--page-bg);
    font-family: "Roboto", Arial, sans-serif;
  }
  .sheet {
    width: 1200px; height: 900px;
    display: flex; align-items: center; justify-content: center; gap: 60px;
  }
  .card {
    position: relative;
    width: 520px; height: 300px;
    border-radius: 22px;
    overflow: hidden;
    box-shadow: 0 6px 18px rgba(0,0,0,.18);
  }
  .card--front { background: var(--card-white); }
  .card--back { background: var(--brand-blue); }

  .card__art { position: absolute; inset: 0; }

  .wordmark { position: absolute; display: flex; align-items: center; gap: 12px; }
  .wordmark__name {
    font-weight: 300; font-size: 66px; line-height: 1; letter-spacing: 2px;
  }
  .wordmark__dot { width: 14px; height: 14px; border-radius: 50%; }
  .wordmark__tag {
    position: absolute; font-weight: 300; font-size: 10px;
    letter-spacing: 6.5px; text-transform: lowercase;
  }

  .card--front .wordmark { left: 44px; top: 26px; }
  .card--front .wordmark__name { color: var(--ink); }
  .card--front .wordmark__dot { background: var(--brand-blue); }
  .card--front .wordmark__tag { left: 48px; top: 104px; color: var(--muted); }

  .contact {
    position: absolute; left: 22px; top: 178px;
    list-style: none; color: var(--on-dark);
    font-size: 13px; line-height: 19px;
  }
  .contact__item { display: flex; align-items: center; gap: 7px; }
  .contact__label { color: var(--brand-blue); }
  .contact__icon { width: 11px; height: 11px; fill: var(--brand-blue); }

  .person { position: absolute; right: 28px; top: 128px; text-align: right; }
  .person__name {
    color: var(--brand-blue); font-weight: 700; font-size: 22px;
    text-transform: uppercase; letter-spacing: .3px;
  }
  .person__role { color: var(--muted); font-size: 15px; margin-top: 2px; }

  .card--back .wordmark { left: 50%; top: 100px; transform: translateX(-50%); }
  .card--back .wordmark__name { color: var(--brand-blue-deep); font-size: 80px; }
  .card--back .wordmark__dot { background: var(--card-white); }
  .card--back .wordmark__tag {
    left: 50%; top: 198px; transform: translateX(-50%);
    color: var(--brand-blue-deep); white-space: nowrap;
  }
</style>
</head>
<body>
<main class="sheet">

  <section class="card card--front" aria-label="Business card front">
    <svg class="card__art" viewBox="0 0 520 300" aria-hidden="true">
      <polygon points="0,162 330,162 372,262 0,262" fill="var(--band-dark)"/>
      <polygon points="330,162 440,162 440,300 372,300 372,262" fill="var(--brand-blue)"/>
      <rect x="492" y="0" width="28" height="22" fill="var(--brand-blue)"/>
    </svg>

    <div class="wordmark">
      <span class="wordmark__name">tbk</span>
      <span class="wordmark__dot"></span>
    </div>
    <span class="wordmark__tag">plumbing services</span>

    <ul class="contact">
      <li class="contact__item"><span class="contact__label">ABN:</span> 73 215 904 386</li>
      <li class="contact__item">
        <svg class="contact__icon" viewBox="0 0 24 24"><path d="M6.6 10.8a15 15 0 0 0 6.6 6.6l2.2-2.2c.3-.3.7-.4 1-.2 1.1.4 2.3.6 3.6.6.6 0 1 .4 1 1V20c0 .6-.4 1-1 1A17 17 0 0 1 3 4c0-.6.4-1 1-1h3.5c.6 0 1 .4 1 1 0 1.3.2 2.5.6 3.6.1.3 0 .7-.2 1z"/></svg>
        0431 286 517
      </li>
      <li class="contact__item">
        <svg class="contact__icon" viewBox="0 0 24 24"><path d="M2 5h20v14H2zm2 2v.5l8 5 8-5V7l-8 5z"/></svg>
        rowan@tbk-plumbing.com.au
      </li>
    </ul>

    <div class="person">
      <p class="person__name">Rowan Keddle</p>
      <p class="person__role">Director</p>
    </div>
  </section>

  <section class="card card--back" aria-label="Business card back">
    <div class="wordmark">
      <span class="wordmark__name">tbk</span>
      <span class="wordmark__dot"></span>
    </div>
    <span class="wordmark__tag">plumbing services</span>
  </section>

</main>
</body>
</html>
```